Corporate Travel Technology Company needs new Business Card design

We need a new business card design to reflect our re-branded company. Our company is called tolvEn (pronounced tolvenn) and we provide Business Intelligence and mobile travel management solutions for the corporate travel industry. Our multinational customers use our solutions to manage large travel budgets and frequent travellers, as well as to save money and reduce risk. We'd like to see designs that use the blue and green palette as well as our corporate logo (attached below). The design should communicate innovation, insight, forward thinking, contemporary, trusted.

Target Market(s)

Large multinational corporates and Travel Agencies.

Industry/Entity Type

Business

Contact Information for Business Card

Rosalind Mercer
Chief Executive
tolvEn
Phone number - +61 (0)2 8134 2907
Email address - rosalind.mercer@tolven-example.com
Mobile number - +61 (0)438 516 702
www.tolven-example.com

Font styles to use
Other font styles liked:
• Please use font as close to corporate logo as possible

Colors
0255a3
0393ce
00a990
33b8a4
33a6d7
3176b5

Requirements
Must have
• Please include the words;
• Mobile Travel Management
• Accelerating Travel Business Insights
• Use corporate logo - although icon can be stylised if needed

```html
<!DOCTYPE html>
<html lang="en">
<head>
<meta charset="utf-8">
<title>tolvEn business card</title>
<link rel="stylesheet" href="https://fonts.googleapis.com/css2?family=Open+Sans:wght@400;600;700&display=swap">
<style>
  :root {
    --backdrop: #d9dadb;
    --paper: #ffffff;
    --sky: #29aae1;
    --slate: #3f5b59;
    --ink: #3a4b4a;
  }
  * { box-sizing: border-box; margin: 0; padding: 0; }
  html, body { width: 1200px; height: 900px; overflow: hidden; }
  body {
    background: var(--backdrop);
    font-family: "Open Sans", Arial, sans-serif;
    position: relative;
  }
  .card {
    position: absolute;
    left: 300px;
    width: 600px;
    height: 343px;
    background: var(--paper);
    box-shadow: 0 6px 18px rgba(0,0,0,0.18);
    overflow: hidden;
  }
  .card--front { top: 60px; }
  .card--back { top: 497px; }

  .brand {
    position: absolute;
    display: flex;
    align-items: center;
    gap: 12px;
  }
  .brand__dot {
    border-radius: 50%;
    background: var(--sky);
  }
  .brand__name {
    color: var(--slate);
    font-weight: 600;
    line-height: 1;
    letter-spacing: 1px;
  }
  .card--front .brand { left: 0; right: 0; top: 78px; justify-content: center; }
  .card--front .brand__dot { width: 30px; height: 30px; }
  .card--front .brand__name { font-size: 82px; }

  .tagline {
    position: absolute;
    left: 0; right: 0;
    text-align: center;
    font-weight: 600;
  }
  .tagline--service { top: 212px; color: var(--sky); font-size: 21px; }
  .tagline--promise { top: 244px; color: var(--ink); font-size: 22px; font-weight: 700; }

  .band {
    position: absolute;
    left: 0;
    right: 0;
  }
  .band--top { top: 0; height: 14px; background: var(--sky); }
  .band--bottom { bottom: 0; height: 28px; background: var(--slate); }

  .card--back .brand { left: 40px; top: 52px; }
  .card--back .brand__dot { width: 22px; height: 22px; }
  .card--back .brand__name { font-size: 60px; }

  .person {
    position: absolute;
    right: 40px;
    top: 160px;
    text-align: right;
  }
  .person__name { color: var(--ink); font-size: 20px; font-weight: 700; }
  .person__role { color: var(--sky); font-size: 16px; }

  .contacts {
    position: absolute;
    right: 22px;
    top: 222px;
    list-style: none;
    color: var(--ink);
    font-size: 15px;
    line-height: 20px;
  }
  .contacts li {
    display: flex;
    justify-content: flex-end;
    align-items: center;
    gap: 8px;
  }
  .contacts svg { width: 11px; height: 11px; fill: var(--sky); flex: none; }
</style>
</head>
<body>

<section class="card card--front">
  <div class="brand">
    <span class="brand__name">tolvEn</span>
    <span class="brand__dot"></span>
  </div>
  <p class="tagline tagline--service">Mobile Travel Management</p>
  <p class="tagline tagline--promise">Accelerating Travel Business Insights</p>
</section>

<section class="card card--back">
  <div class="band band--top"></div>
  <div class="band band--bottom"></div>

  <div class="brand">
    <span class="brand__name">tolvEn</span>
    <span class="brand__dot"></span>
  </div>

  <div class="person">
    <p class="person__name">Rosalind Mercer</p>
    <p class="person__role">Chief Executive</p>
  </div>

  <ul class="contacts">
    <li>+61 (0)2 8134 2907
      <svg viewBox="0 0 12 12"><path d="M1 4 Q6 0 11 4 L9 6 L7.5 4.5 H4.5 L3 6 Z M3 7 H9 V11 H3 Z"/></svg></li>
    <li>+61 (0)438 516 702
      <svg viewBox="0 0 12 12"><rect x="3" y="0.5" width="6" height="11" rx="1.2"/></svg></li>
    <li>rosalind.mercer@tolven-example.com
      <svg viewBox="0 0 12 12"><path d="M0.5 2.5 H11.5 V9.5 H0.5 Z"/></svg></li>
    <li>www.tolven-example.com
      <svg viewBox="0 0 12 12"><path d="M2 7 L5 4 L6 5 L3 8 Z M6 4 L9 1 L11 3 L8 6 L7 5 L9 3 L8.5 2.5 L7 4 Z M1 9 L3 11 L2 11.8 L0.2 10 Z"/></svg></li>
  </ul>
</section>

</body>
</html>
```